Modern looking signage for dental office.

Exterior signage for passing cars
Updates
Need extra days to review
Target Market(s)
Cars passing by
Font styles to use
Sans Serif
Colors
3276b5
Requirements
Must have
- Logo
- OPEN ON SUTURDAY AND SUNDAY
- NIGHT CLINIC AVAILABLE
- PLEASE USE THE FONT TYPE IN FILE 4 UPLOADED BELOW.
- (847) 302-7469
- Modern looking

```html
<!DOCTYPE html>
<html lang="en">
<head>
<meta charset="utf-8">
<title>Apex Dental – Exterior Sign</title>
<link rel="stylesheet" href="https://fonts.googleapis.com/css2?family=Open+Sans:wght@300;400;700;800&family=Montserrat:wght@800&display=swap">
<style>
  :root {
    --brand-blue: #3276b5;
    --ink: #111111;
    --logo-grey: #4a4848;
    --wave-grey: #555252;
    --rule-grey: #b9b9b9;
    --backdrop: #9a9a9a;
    --sign-top: #ffffff;
    --sign-bottom: #e4e4e4;
    --white: #ffffff;
  }
  html, body {
    margin: 0;
    width: 1200px;
    height: 1000px;
    overflow: hidden;
    background: var(--backdrop);
    font-family: "Open Sans", Arial, sans-serif;
  }
  .sign {
    position: absolute;
    left: 192px;
    top: 92px;
    width: 816px;
    height: 816px;
    background: linear-gradient(to bottom, var(--sign-top) 0%, var(--sign-bottom) 78%);
    overflow: hidden;
  }
  .brand {
    position: absolute;
    left: 66px;
    top: 52px;
    display: flex;
    align-items: center;
  }
  .brand-mark {
    width: 143px;
    height: 143px;
    border: 2px solid var(--logo-grey);
    border-radius: 50%;
    box-sizing: border-box;
  }
  .brand-name {
    margin-left: 16px;
    font-weight: 300;
    font-size: 76px;
    letter-spacing: 1px;
    color: var(--logo-grey);
    line-height: 1;
    white-space: nowrap;
  }
  .tagline {
    position: absolute;
    left: 280px;
    top: 176px;
    width: 400px;
    text-align: center;
    font-weight: 400;
    font-size: 29px;
    color: var(--logo-grey);
    white-space: nowrap;
  }
  .headline {
    position: absolute;
    left: 0;
    width: 816px;
    text-align: center;
    font-weight: 800;
    line-height: 1;
    white-space: nowrap;
    margin: 0;
  }
  .headline-blue { color: var(--brand-blue); font-size: 110px; letter-spacing: 1px; }
  .headline-dark { color: var(--ink); font-weight: 700; }
  .open-on { top: 275px; }
  .weekend { top: 385px; font-size: 52px; }
  .divider {
    position: absolute;
    left: 174px;
    top: 457px;
    width: 468px;
    height: 2px;
    background: var(--rule-grey);
  }
  .night-clinic { top: 475px; font-size: 104px; }
  .available { top: 572px; font-size: 72px; }
  .waves {
    position: absolute;
    left: 0;
    top: 0;
  }
  .phone {
    position: absolute;
    left: 104px;
    top: 706px;
    display: flex;
    align-items: center;
    gap: 22px;
  }
  .phone-number {
    font-family: "Montserrat", "Open Sans", sans-serif;
    font-weight: 800;
    font-size: 86px;
    color: var(--white);
    letter-spacing: 1px;
    line-height: 1;
  }
</style>
</head>
<body>
  <div class="sign">
    <svg class="waves" width="816" height="816" viewBox="0 0 816 816" aria-hidden="true">
      <path d="M0 638 Q 380 690 816 606 L816 630 Q 400 700 0 652 Z" fill="var(--wave-grey)"/>
      <path d="M0 652 Q 400 700 816 630 L816 816 L0 816 Z" fill="var(--brand-blue)"/>
    </svg>

    <div class="brand">
      <div class="brand-mark"></div>
      <div class="brand-name">APEX DENTAL</div>
    </div>
    <div class="tagline">MODERN GENERAL DENTISTRY</div>

    <p class="headline headline-blue open-on">OPEN ON</p>
    <p class="headline headline-dark weekend">SATURDAY AND SUNDAY</p>
    <div class="divider"></div>
    <p class="headline headline-blue night-clinic">NIGHT CLINIC</p>
    <p class="headline headline-dark available">AVAILABLE</p>

    <div class="phone">
      <svg class="phone-icon" width="70" height="70" viewBox="0 0 70 70" aria-hidden="true">
        <circle cx="35" cy="35" r="33" fill="var(--white)"/>
        <circle cx="35" cy="35" r="27" fill="none" stroke="var(--brand-blue)" stroke-width="2"/>
        <path d="M24 20 C20 22 19 27 21 32 C24 40 30 46 38 49 C43 51 48 50 50 46 L46 41 C45 40 43 40 42 41 L39 43 C34 41 29 36 27 31 L29 28 C30 27 30 25 29 24 Z" fill="var(--brand-blue)"/>
        <path d="M38 22 A12 12 0 0 1 48 32" fill="none" stroke="var(--brand-blue)" stroke-width="2.5" stroke-linecap="round"/>
        <path d="M38 28 A6 6 0 0 1 42 32" fill="none" stroke="var(--brand-blue)" stroke-width="2.5" stroke-linecap="round"/>
      </svg>
      <span class="phone-number">847 302 7469</span>
    </div>
  </div>
</body>
</html>
```